Smart Routing SaaS needs a magic web design

We need a web design that focuses in the UX and conveys the idea of doing magic through our software. The company name is Brantiq and it is a word game about wow and slip... we are a software as a service B2B that helps companies automate dispatches and routes for their delivery guys to deliver goods to the customers. Think of it as an zephyr software applicable to your own fleet or third party fleets that can be used for example in a supermarket. That way the final user (buyer of the supermarket) knows where the parcel is, if it is leaving the store, if it is on its way, how long will it take to arrive, who is the delivery guy, etc... Brantiq's symbol is an owl. Think of it as the movie The Lanternkeep: Autumn's Oath, Queen Odalie had an owl mask and the ice owl who was her eyes on the field... that is the idea I want to convey through this software. It is the eyes for the business and the eyes for the final user. The software is comprised of a web platform (for the business with the fleet to manage) and the driver's application. The final customer receives the real time tracking information through SMS and email. The design should communicate magic through the use of the software... You can see some info on the existing webpage... which is very cold and dull... no life in it brantiq.example.. Use of gifs is desirable.

Text that can be used on the cover to convey main idea:

High end technology
We take care of your delivery management

The software that brings visibility and smartness to your deliveries through automated dispatches and smart routings
Our expertise: A Delightful Customer Experience of Deliveries

Target Market(s)

Professionals and businesses of all types with a delivery of any kind (supermarkets, pharmacies, restaurants, moving services, fleets, home services, deliveries, supply chain, field sales...)
Please look at competition webpages:
www.pathkit7.example
www.movra.example
www.trekly.example
vantacor.example
quickbarn.example
zephyr dash

Industry/Entity Type

Business Software

Coding

Coded - Design and coding required

Number of Pages Required

5+ page

Font styles to use
Other font styles liked:
• Modulus and Trade Gothic Ltd

Requirements
Must have
• MUST HAVE A D3JS LIKE:
• http://grafnode.example/jterran/5518302
• http://jterran.codepages.example/d3/talk/20111116/force-collapsible.html
• https://plinthware.example/hugo/fisheye/
• http://movingcharts.example/lab/d3-tree/
• A great magic capturing Homepage that conveys the main idea of what we are. A software that will help you manage your people on field who are getting something to the end customer (who will be aware of the live parcel status through SMS/ email notifications), we live in the cloud... no need of implementation fees, there is a free demo. Right now the webpage has an animation. Maybe a picture with a video on it could be something nice, or something that moves... take a look at zephyr dash. The main idea of the page should send the idea of something magic... use the owl... something that flies.
• The page must have gifs here and there... never stop the idea of a swift magic going on... efficiency on the logistics management of the company... happy customers.
• Parallax... I love parallax.
Nice to have
• The webpage may be telling a story... first what are we and what we do... how it works, who is our market, the benefits, hard facts on efficiency... please take a look at the current webpage www.brantiq.example to get more info but make it beautiful.
• A phrase here and there of why they need our service
Should not have
• I want to change the current idea of the webpage that the software aims only to manage fleets for home delivery... we are NOT a home delivery only management system. We can make any company's logistics "fly".
• I dont want to see dullness in the webpage, I am looking for a soul.

```html
<!DOCTYPE html>
<html lang="en">
<head>
<meta charset="utf-8">
<title>Brantiq — Contact</title>
<link rel="stylesheet" href="https://fonts.googleapis.com/css2?family=Roboto:ital,wght@0,300;0,400;0,500;0,700;1,300&display=swap">
<style>
  :root {
    --teal: #12a6c4;
    --teal-dark: #0a8fab;
    --hero-a: #0b6f82;
    --hero-b: #15899c;
    --ink: #3d3d3d;
    --muted: #8a8a8a;
    --field-bg: #f8f8f8;
    --field-line: #dedede;
    --footer: #2b2a2a;
    --footer-base: #1d1c1c;
    --footer-text: #d6d6d6;
    --white: #ffffff;
  }
  * { box-sizing: border-box; margin: 0; padding: 0; }
  html, body { width: 1138px; height: 1200px; overflow: hidden; background: var(--white); }
  body { position: relative; font-family: 'Roboto', Arial, sans-serif; color: var(--ink); }
  .abs { position: absolute; }

  /* header */
  .site-header { position: absolute; left: 0; top: 0; width: 1138px; height: 107px; border-top: 3px solid var(--teal); background: var(--white); }
  .brand { position: absolute; left: 93px; top: 36px; display: flex; align-items: center; gap: 8px; color: var(--teal); font-size: 32px; font-weight: 300; letter-spacing: 1px; }
  .brand-dot { width: 7px; height: 7px; border-radius: 50%; background: var(--teal); }
  .main-nav a { position: absolute; top: 49px; font-size: 13px; font-weight: 300; color: #555; text-decoration: none; }
  .main-nav a.is-active { color: var(--teal); }

  /* hero */
  .hero { position: absolute; left: 0; top: 107px; width: 1138px; height: 293px; background: radial-gradient(ellipse at 50% 45%, var(--hero-b), var(--hero-a) 75%); }
  .hero-shadow { position: absolute; left: 40px; top: 400px; width: 1058px; height: 24px; background: radial-gradient(ellipse at 50% 0%, rgba(0,0,0,.12), rgba(0,0,0,0) 70%); }
  .hero-title { position: absolute; left: 0; width: 1138px; text-align: center; color: var(--white); font-weight: 700; text-shadow: 0 2px 3px rgba(0,0,0,.35); }
  .hero-title.main { top: 205px; font-size: 40px; letter-spacing: .5px; }
  .hero-title.sub { top: 263px; font-size: 33px; font-weight: 500; }
  .hero-arrow { position: absolute; top: 234px; width: 34px; height: 34px; }

  /* contact form */
  .section-title { position: absolute; left: 93px; top: 451px; font-size: 29px; font-weight: 400; color: #4a4a4a; }
  .section-title span { color: var(--teal); }
  .field { position: absolute; height: 38px; background: var(--field-bg); border: 1px solid var(--field-line); border-radius: 2px; font-size: 13px; font-weight: 300; color: var(--muted); padding: 0 14px; display: flex; align-items: center; justify-content: space-between; }
  .field svg { width: 13px; height: 13px; fill: #666; }
  .field.message { align-items: flex-start; padding-top: 13px; }
  .submit { position: absolute; left: 93px; top: 853px; width: 157px; height: 45px; background: linear-gradient(#19b3d1, var(--teal-dark)); color: var(--white); font-size: 16px; font-weight: 400; display: flex; align-items: center; justify-content: center; border-radius: 2px; }

  /* address */
  .map-frame { position: absolute; left: 710px; top: 456px; width: 335px; height: 212px; border: 1px solid #e3e3e3; padding: 4px; background: var(--white); box-shadow: 0 0 3px rgba(0,0,0,.08); }
  .map-fill { width: 100%; height: 100%; background: linear-gradient(135deg, #e9efe2, #f1f1ee 55%, #eef0f2); }
  .address-title { position: absolute; left: 710px; top: 693px; font-size: 16px; font-weight: 400; color: #3f3f3f; }
  .address-rule { position: absolute; left: 710px; top: 726px; width: 335px; height: 1px; background: #e4e4e4; }
  .address-item { position: absolute; left: 750px; font-size: 12.5px; font-weight: 300; color: #666; line-height: 16px; }
  .address-icon { position: absolute; left: 710px; width: 16px; height: 16px; fill: var(--teal); }

  /* footer */
  .site-footer { position: absolute; left: 0; top: 950px; width: 1138px; height: 189px; background: var(--footer); }
  .footer-heading { position: absolute; top: 991px; font-size: 16px; font-weight: 400; color: var(--white); }
  .footer-list { position: absolute; top: 1024px; list-style: none; font-size: 11.5px; font-weight: 300; color: var(--footer-text); line-height: 20.3px; }
  .footer-contact { position: absolute; left: 576px; top: 1035px; font-size: 11.5px; font-weight: 300; color: var(--footer-text); line-height: 20.3px; }
  .newsletter-input { position: absolute; left: 848px; top: 1031px; width: 197px; height: 39px; background: #363535; color: #8d8d8d; font-size: 10px; font-style: italic; font-weight: 300; padding: 0 13px; display: flex; align-items: center; }
  .newsletter-send { position: absolute; left: 967px; top: 1084px; width: 78px; height: 27px; background: var(--teal); border-radius: 2px; color: var(--white); font-size: 11.5px; font-weight: 500; display: flex; align-items: center; justify-content: center; }
  .footer-base { position: absolute; left: 0; top: 1139px; width: 1138px; height: 61px; background: var(--footer-base); }
  .copyright { position: absolute; left: 0; width: 1138px; top: 1163px; text-align: center; font-size: 11.5px; font-weight: 400; color: var(--white); }
</style>
</head>
<body>

<header class="site-header">
  <div class="brand"><span class="brand-dot"></span>Brantiq</div>
  <nav class="main-nav">
    <a href="#" style="left:523px">HOME</a>
    <a href="#" style="left:604px">PLATFORM</a>
    <a href="#" style="left:715px">ABOUT</a>
    <a href="#" class="is-active" style="left:801px">CONTACT</a>
    <a href="#" style="left:903px">REGISTER</a>
    <a href="#" style="left:1007px">LOGIN</a>
  </nav>
</header>

<section class="hero" role="img" aria-label="Teal world map illustration with delivery location pins joined by dashed route lines"></section>
<div class="hero-shadow"></div>
<h1 class="hero-title main">CONTACT US</h1>
<p class="hero-title sub">MANAGER OF YOUR DELIVERIES</p>
<svg class="hero-arrow" style="left:25px" viewBox="0 0 34 34" aria-label="Previous slide"><circle cx="17" cy="17" r="15.5" fill="none" stroke="#fff" stroke-width="2"/><path d="M19.5 10.5 13 17l6.5 6.5" fill="none" stroke="#fff" stroke-width="2"/></svg>
<svg class="hero-arrow" style="left:1072px" viewBox="0 0 34 34" aria-label="Next slide"><circle cx="17" cy="17" r="15.5" fill="none" stroke="#fff" stroke-width="2"/><path d="M14.5 10.5 21 17l-6.5 6.5" fill="none" stroke="#fff" stroke-width="2"/></svg>

<main>
  <h2 class="section-title">CONTACT <span>US</span></h2>

  <form class="contact-form">
    <div class="field" style="left:93px;top:515px;width:266px">Name
      <svg viewBox="0 0 16 16"><circle cx="8" cy="4.5" r="3.5"/><path d="M1.5 16c0-4 2.8-6.5 6.5-6.5s6.5 2.5 6.5 6.5z"/></svg></div>
    <div class="field" style="left:372px;top:515px;width:266px">Surname
      <svg viewBox="0 0 16 16"><circle cx="8" cy="4.5" r="3.5"/><path d="M1.5 16c0-4 2.8-6.5 6.5-6.5s6.5 2.5 6.5 6.5z"/></svg></div>

    <div class="field" style="left:93px;top:567px;width:173px">Company
      <svg viewBox="0 0 16 16"><path d="M3 6l5 5 5-5" fill="none" stroke="#666" stroke-width="1.6"/></svg></div>
    <div class="field" style="left:279px;top:567px;width:173px">Country
      <svg viewBox="0 0 16 16"><path d="M3 6l5 5 5-5" fill="none" stroke="#666" stroke-width="1.6"/></svg></div>
    <div class="field" style="left:464px;top:567px;width:173px">State
      <svg viewBox="0 0 16 16"><path d="M3 6l5 5 5-5" fill="none" stroke="#666" stroke-width="1.6"/></svg></div>

    <div class="field" style="left:93px;top:621px;width:266px">Email
      <svg viewBox="0 0 16 16"><path d="M1 3h14v2L8 9.5 1 5z"/><path d="M1 6.8l7 4.5 7-4.5V13H1z"/></svg></div>
    <div class="field" style="left:372px;top:621px;width:266px">Telephone
      <svg viewBox="0 0 16 16"><path d="M3.5 1l3 3.2-1.8 2a9 9 0 0 0 5.1 5.1l2-1.8L15 12.5 13 15C6.5 15 1 9.5 1 3z"/></svg></div>

    <div class="field message" style="left:93px;top:673px;width:544px;height:145px">Message
      <svg viewBox="0 0 16 16"><path d="M2 4h6M2 4v10h10V9" fill="none" stroke="#666" stroke-width="1.5"/><path d="M12.5 1.5l2 2L8 10H6V8z"/></svg></div>

    <div class="submit">Submit Now</div>
  </form>

  <aside>
    <div class="map-frame"><div class="map-fill" role="img" aria-label="Road map of the office location"></div></div>
    <h3 class="address-title">ADDRESS</h3>
    <div class="address-rule"></div>

    <svg class="address-icon" style="top:745px" viewBox="0 0 16 16"><path d="M8 0.5a5 5 0 0 0-5 5c0 3.7 5 10 5 10s5-6.3 5-10a5 5 0 0 0-5-5zm0 7a2 2 0 1 1 0-4 2 2 0 0 1 0 4z"/></svg>
    <p class="address-item" style="top:745px">Address : 200 Latin words, combined<br>with a handful</p>

    <svg class="address-icon" style="top:793px" viewBox="0 0 16 16"><path d="M3.5 1l3 3.2-1.8 2a9 9 0 0 0 5.1 5.1l2-1.8L15 12.5 13 15C6.5 15 1 9.5 1 3z"/></svg>
    <p class="address-item" style="top:793px">Ph : 5550142387 / 5550142387</p>

    <svg class="address-icon" style="top:823px" viewBox="0 0 16 16"><rect x="1" y="3" width="14" height="10" rx="1" fill="none" stroke="#12a6c4" stroke-width="1.5"/><path d="M1.5 3.8 8 9l6.5-5.2" fill="none" stroke="#12a6c4" stroke-width="1.5"/></svg>
    <p class="address-item" style="top:825px">E mail : info@brantiq.example</p>
  </aside>
</main>

<footer>
  <div class="site-footer"></div>
  <h4 class="footer-heading" style="left:97px">COMPANY</h4>
  <ul class="footer-list" style="left:95px"><li>Support</li><li>Price</li><li>Sign up</li><li>Contact</li></ul>

  <h4 class="footer-heading" style="left:251px">COMMUNITY</h4>
  <ul class="footer-list" style="left:249px"><li>Guiglines</li><li>Terms and conditions</li><li>privacy policy</li><li>site map</li></ul>

  <h4 class="footer-heading" style="left:437px">FOLLOW US</h4>
  <ul class="footer-list" style="left:437px"><li>Friendloop</li><li>Chirpline</li><li>Snapframe</li><li>Searchwell</li></ul>

  <h4 class="footer-heading" style="left:606px">CONTACT US</h4>
  <p class="footer-contact">Address : 200 Latin words, combined<br>with a handful<br>Ph : 5550142387 / 5550142387<br>E mail : info@brantiq.example</p>

  <h4 class="footer-heading" style="left:847px">NEWSLETTER</h4>
  <div class="newsletter-input">Enter The Mail Id</div>
  <div class="newsletter-send">Send Now</div>

  <div class="footer-base"></div>
  <p class="copyright">Copyrights@2016Company name all rights reserved</p>
</footer>

</body>
</html>
```